Velmora Systems Website

Website design for our company: Velmora Systems.
The website should look fresh and IT focused. Please have a look at http://www.velmorasystems.example.au/ for our current design. We want something fresh and new, professional looking, in WordPress so we can easily make changes.

It Company

```html
<!DOCTYPE html>
<html lang="en">
<head>
<meta charset="utf-8">
<title>Velmora Systems</title>
<link rel="stylesheet" href="https://fonts.googleapis.com/css2?family=Open+Sans:wght@300;400;600;700&display=swap">
<style>
:root{
  --green:#0fae4f;
  --green-light:#35c46c;
  --green-dark:#0a9642;
  --blue:#1267b8;
  --ink:#3a3a3c;
  --muted:#555;
  --page:#f3f3f3;
  --band:#e8e8e8;
  --footer:#47474a;
  --footer-text:#cfcfcf;
  --footer-head:#bdbdbd;
  --bubble:#8c8e92;
}
*{margin:0;padding:0;box-sizing:border-box}
html,body{width:1024px;height:1200px;overflow:hidden}
body{position:relative;font-family:"Open Sans",Arial,sans-serif;background:var(--page);color:var(--ink)}
.abs{position:absolute}

.topline{left:0;top:0;width:1024px;height:3px;background:var(--blue)}
.header{left:0;top:3px;width:1024px;height:75px;background:#f4f4f4}
.brand{left:136px;top:8px;width:130px;height:64px;background:var(--green);border:3px solid #0b8c3f;border-radius:3px;display:flex;align-items:center;justify-content:center;gap:6px}
.brand-dot{width:14px;height:14px;border-radius:50%;background:#fff}
.brand-name{color:#fff;font-weight:700;font-size:13px}

.remote{left:632px;top:0;width:264px;height:42px;background:var(--blue);border-radius:0 0 6px 6px}
.remote-label{left:15px;top:8px;color:#fff;font-weight:700;font-size:11px;line-height:13px}
.code-field{left:80px;top:8px;width:176px;height:26px;background:#3d3f44;border-radius:4px;border:1px solid #2c2d31}
.code-field span{position:absolute;left:8px;top:7px;font-size:7.5px;color:#d0d0d0}
.btn-connect{position:absolute;right:2px;top:2px;width:52px;height:20px;border:1px solid #6a6b70;border-radius:3px;background:#4b4c51;color:#ddd;font-size:7.5px;display:flex;align-items:center;justify-content:center}

.nav{left:0;top:78px;width:1024px;height:36px;background:linear-gradient(#30c263,var(--green-dark))}
.nav a{position:absolute;top:12px;color:#fff;font-weight:700;font-size:11px;text-decoration:none}
.search{left:712px;top:4px;width:176px;height:27px;background:#f4f4f4;border-radius:3px}
.search span{position:absolute;left:8px;top:7px;font-size:10px;color:#999}
.search svg{position:absolute;right:8px;top:6px}

.hero{left:0;top:114px;width:1024px;height:324px;background:radial-gradient(ellipse at 45% 30%,#5fb8c9 0%,#2d5768 30%,#1c2733 65%,#131a22 100%)}
.arrow{top:145px;width:37px;height:37px;border-radius:50%;display:flex;align-items:center;justify-content:center;color:#fff;font-size:12px;font-weight:700}
.arrow.prev{left:90px;background:#1d64b0;border:2px solid #5a8fc7}
.arrow.next{left:894px;background:#3e4046;border:2px solid #6a6c72}

.mission{left:0;top:438px;width:1024px;height:84px;background:linear-gradient(90deg,var(--green) 0%,var(--green-light) 45%,var(--green) 100%)}
.mission h1{position:absolute;left:137px;top:16px;font-weight:300;font-size:24px;color:#fff;white-space:nowrap}
.mission p{position:absolute;left:141px;top:45px;font-size:14.5px;color:#fff;white-space:nowrap}

.services-title{left:0;top:546px;width:1000px;text-align:center;font-weight:300;font-size:19px;color:#444}
.rule{left:136px;top:588px;width:752px;height:2px;background:#d8d8d8}
.rule-notch{left:506px;top:589px;width:0;height:0;border-left:5px solid transparent;border-right:5px solid transparent;border-top:5px solid #d8d8d8}
.service{display:flex;align-items:center;gap:8px;width:190px}
.service .ico{flex:none;width:32px;height:32px;border-radius:50%;background:#3b3c40;display:flex;align-items:center;justify-content:center}
.service.active .ico{background:#2a87d0;border:2px solid #9cc7ea}
.service b{font-size:11.5px;font-weight:700;color:#3a3a3c;line-height:16px}
.service.active b{color:var(--blue)}

.welcome-band{left:0;top:762px;width:1024px;height:208px;background:var(--band)}
.section-head{top:790px;font-weight:300;font-size:19.5px;color:#444}
.avatar{border-radius:50%;background:linear-gradient(#8a8a8a,#4b4b4b);border:4px solid #f4f4f4;box-shadow:0 0 0 1px #bbb}
.welcome-text{left:218px;top:826px;width:255px;font-size:10.5px;line-height:16px;color:#444}
.btn-more{left:219px;top:912px;width:82px;height:26px;border:1px solid #c9c9c9;border-radius:3px;background:#f3f3f3;font-size:7.5px;color:#555;display:flex;align-items:center;justify-content:center}
.person{left:522px;top:886px;font-size:8.5px;line-height:10px;color:#333}
.person b{font-weight:700}
.person span{font-size:7.5px}
.bubble{left:612px;top:831px;width:276px;height:103px;background:var(--bubble);border-radius:3px;box-shadow:0 3px 0 #bdbdbd}
.bubble-tip{left:594px;top:844px;width:0;height:0;border-top:0 solid transparent;border-bottom:22px solid transparent;border-right:20px solid var(--bubble)}
.bubble p{position:absolute;left:25px;top:20px;width:235px;font-size:10.5px;line-height:16px;color:#fff}

.footer{left:0;top:970px;width:1024px;height:216px;background:var(--footer)}
.footer-brand{left:138px;top:34px;width:148px;height:76px;background:var(--green);border:3px solid #dfe9e2;border-radius:3px;display:flex;align-items:center;justify-content:center;gap:7px}
.footer-brand .brand-name{font-size:15px}
.copyright{left:137px;top:161px;font-size:9px;color:#8a8a8a}
.f-head{top:36px;font-size:11px;font-weight:700;color:var(--footer-head)}
.f-list{left:365px;top:64px;list-style:none;font-size:10.5px;line-height:16px;color:var(--footer-text)}
.f-list li::before{content:"";display:inline-block;border-left:3.5px solid #bbb;border-top:3.5px solid transparent;border-bottom:3.5px solid transparent;margin-right:5px;vertical-align:1px}
.f-contacts{left:521px;top:64px;font-size:10.5px;line-height:16px;color:var(--footer-text)}
.f-remote{left:713px;top:65px;font-size:9.5px;color:var(--footer-text)}
.f-input{left:713px;top:90px;width:175px;height:26px;background:#3d3e42;border-radius:3px;border:1px solid #333}
.f-input .btn-connect{background:#4b4c51}
.social{top:162px;width:13px;height:13px;border-radius:50%;background:#6f7075}
.bottomline{left:0;top:1186px;width:1024px;height:14px;background:var(--green)}
</style>
</head>
<body>
<div class="abs topline"></div>
<header class="abs header">
  <div class="abs brand" style="top:5px"><span class="brand-dot"></span><span class="brand-name">Velmora Systems</span></div>
</header>

<div class="abs remote">
  <div class="abs remote-label">REMOTE<br>SUPPORT</div>
  <div class="abs code-field"><span>ENTER -6 DIGIT CODE</span><div class="btn-connect">CONNECT</div></div>
</div>

<nav class="abs nav">
  <a style="left:152px">HOME</a>
  <a style="left:244px">SERVICES</a>
  <a style="left:356px">PORTFOLIO</a>
  <a style="left:478px">ABOUT</a>
  <a style="left:581px">CONTACTS</a>
  <div class="abs search"><span>Search the site</span>
    <svg width="14" height="14" viewBox="0 0 14 14"><circle cx="8.5" cy="5.5" r="4" fill="none" stroke="#666" stroke-width="1.3"/><line x1="5.5" y1="8.5" x2="1" y2="13" stroke="#666" stroke-width="1.5"/></svg>
  </div>
</nav>

<section class="abs hero" role="img" aria-label="Businessman in suit touching glowing hexagon interface">
  <div class="abs arrow prev">&lsaquo;</div>
  <div class="abs arrow next">&rsaquo;</div>
</section>

<section class="abs mission">
  <h1>Velmora Systems is an Adelaide based company with a single objective</h1>
  <p>- to excel in the support and service of all computer and IT needs.</p>
</section>

<h2 class="abs services-title" style="left:12px">OUR SERVICES</h2>
<div class="abs rule"></div>
<div class="abs rule-notch"></div>

<div class="abs service active" style="left:136px;top:616px"><span class="ico"><svg width="14" height="12"><rect x="1" y="1" width="12" height="9" rx="4" fill="#fff"/><line x1="4" y1="5.5" x2="10" y2="5.5" stroke="#2a87d0"/></svg></span><b>ON-SITE SERVICE</b></div>
<div class="abs service" style="left:328px;top:616px"><span class="ico"><svg width="14" height="14"><rect x="3" y="3" width="8" height="8" fill="none" stroke="#fff" stroke-width="1.5"/><rect x="1" y="1" width="3" height="3" fill="#fff"/><rect x="10" y="1" width="3" height="3" fill="#fff"/><rect x="1" y="10" width="3" height="3" fill="#fff"/><rect x="10" y="10" width="3" height="3" fill="#fff"/></svg></span><b>MEDICAL IT SERVICE</b></div>
<div class="abs service" style="left:521px;top:616px"><span class="ico"><svg width="16" height="16"><circle cx="8" cy="8" r="7" fill="#fff"/><path d="M4 5 L8 4 L9 8 L6 11 Z" fill="#3b3c40"/></svg></span><b>REMOTE DESKTOP</b></div>
<div class="abs service" style="left:713px;top:616px"><span class="ico"><svg width="14" height="14"><path d="M5 1 H9 V5 L13 13 H1 L5 5 Z" fill="#fff"/></svg></span><b>PHARMACY IT SERVICE</b></div>

<div class="abs service" style="left:136px;top:675px"><span class="ico"><svg width="12" height="14"><path d="M1 1 H8 L11 4 V13 H1 Z" fill="none" stroke="#fff" stroke-width="1.4"/><circle cx="6" cy="8" r="2" fill="#fff"/></svg></span><b>HARDWARE/ SOFTWARE SUPPLY</b></div>
<div class="abs service" style="left:328px;top:674px"><span class="ico"><svg width="14" height="14"><path d="M12 1 L13 2 L5 11 L3 9 Z" fill="#fff"/><path d="M3 10 L4 11 L1 13 Z" fill="#fff"/></svg></span><b>WEBSITE DESIGN</b></div>
<div class="abs service" style="left:521px;top:674px"><span class="ico"><svg width="16" height="16"><path d="M8 1 L15 8 L8 15 L1 8 Z" fill="#fff"/><path d="M6 6 L10 10 M10 6 L6 10" stroke="#3b3c40" stroke-width="1.5"/></svg></span><b>DISASTER RECOVERY</b></div>
<div class="abs service" style="left:713px;top:674px"><span class="ico"><svg width="14" height="14"><g stroke="#fff" stroke-width="1.4"><line x1="2" y1="1" x2="2" y2="13"/><line x1="5.5" y1="1" x2="5.5" y2="13"/><line x1="9" y1="1" x2="9" y2="13"/><line x1="12.5" y1="1" x2="12.5" y2="13"/></g><g fill="#fff"><rect x="0.5" y="4" width="3" height="2"/><rect x="4" y="8" width="3" height="2"/><rect x="7.5" y="3" width="3" height="2"/><rect x="11" y="9" width="3" height="2"/></g></svg></span><b>CONSUMABLES</b></div>

<section class="abs welcome-band"></section>
<h2 class="abs section-head" style="left:138px">WELCOME TO OUR SITE!</h2>
<div class="abs avatar" style="left:138px;top:830px;width:68px;height:68px" role="img" aria-label="Portrait photo of a smiling man"></div>
<p class="abs welcome-text">Because we know you don't want to be limited on a portrait or scape format we made Showcase. compatible in both portrait AND landscape! Yes, we care about you.</p>
<div class="abs btn-more">READ MORE</div>

<h2 class="abs section-head" style="left:521px">WHAT PEOPLE SAY</h2>
<div class="abs avatar" style="left:522px;top:830px;width:52px;height:52px;background:linear-gradient(#a08c7a,#5a4a40)" role="img" aria-label="Portrait photo of a smiling woman"></div>
<div class="abs person"><b>MARA LINDQVIST</b><br><span>CEO, LINDQVIST.EXAMPLE</span></div>
<div class="abs bubble-tip"></div>
<div class="abs bubble"><p>Because we know you don't want to be limited on a portrait or scape format we made Showcase. compatible in both portrait AND landscape!</p></div>

<footer class="abs footer">
  <div class="abs footer-brand"><span class="brand-dot"></span><span class="brand-name">Velmora Systems</span></div>
  <div class="abs copyright">© 2014 Velmora Systems. All Rights Reserved</div>

  <div class="abs f-head" style="left:365px">NAVIGATION</div>
  <ul class="abs f-list">
    <li>HOME</li><li>CLIENTS</li><li>SERVICES</li><li>SUPPORTS</li><li>TESTIMONIALS</li><li>CONTACT US</li><li>ABOUT US</li>
  </ul>

  <div class="abs f-head" style="left:521px">CONTACTS</div>
  <div class="abs f-contacts">Kestrel Works Inc.<br>PO Box 40518<br>Harlow Lane, Melbourne<br>Victoria 8020 Australia<br><br>Phone: (415) 555-0148<br>support@velmorasystems.example</div>

  <div class="abs f-head" style="left:713px">REMOTE SUPPORT</div>
  <div class="abs f-remote">Enter you 6-digit code</div>
  <div class="abs f-input"><div class="btn-connect">CONNECT</div></div>
  <div class="abs f-head" style="left:713px;top:137px">GET SOCIAL</div>
  <span class="abs social" style="left:713px"></span>
  <span class="abs social" style="left:741px"></span>
  <span class="abs social" style="left:769px"></span>
  <span class="abs social" style="left:797px"></span>
  <span class="abs social" style="left:825px"></span>
</footer>
<div class="abs bottomline"></div>
</body>
</html>
```